business card for horse saddlery

after a new business card for our saddlery, i will add 2 logos we have previously used and they can be used (or not) . Any images can be used from our website also at www.harrowfields.net.au, I have also added our brand logo, which may be good to incorporate on back ? we have over 15, 000 items online, ship Australia Wide.

Target Market(s)

horse owners

Industry/Entity Type

Retail - Equestrian

Contact Information for Business Card

Harrowfield Horse Supplies, 1300 48 62 90, www.harrowfields.net.au, 27 Lindqvist Rd Marrowbank Q 4587

Requirements
Must have
• trailgem is our brand so trailgem logo on back as 'distributers of', easy to read
Nice to have
• professional but fun
Should not have
• double sided (description wont save double sided)

```html
<!DOCTYPE html>
<html lang="en">
<head>
<meta charset="utf-8">
<title>Harrowfield Horse Supplies – Business Card</title>
<link href="https://fonts.googleapis.com/css2?family=Poppins:wght@400;500;600;700&display=swap" rel="stylesheet">
<style>
  :root {
    --backdrop: #c4c4c4;
    --card-navy: #0a1a2f;
    --accent-blue: #3d9be0;
    --text-white: #ffffff;
    --sketch-tone: rgba(190, 208, 230, 0.42);
    --faint-tone: rgba(150, 175, 205, 0.16);
  }
  * { box-sizing: border-box; margin: 0; padding: 0; }
  html, body {
    width: 751px; height: 1200px; overflow: hidden;
    background: var(--backdrop);
    font-family: "Poppins", sans-serif;
  }
  .sheet { position: relative; width: 751px; height: 1200px; }
  .card {
    position: absolute; top: 343px;
    width: 294px; height: 514px;
    background: var(--card-navy);
    color: var(--text-white);
    overflow: hidden;
    box-shadow: 6px 8px 14px rgba(0,0,0,0.28);
  }
  .card--front { left: 64px; }
  .card--back { left: 398px; }

  /* Front */
  .brand-mark {
    position: absolute; left: 38px; top: 62px;
    display: flex; align-items: center; gap: 9px;
    font-size: 22px; font-weight: 600; letter-spacing: 0.3px;
  }
  .brand-mark__dot {
    width: 18px; height: 18px; border-radius: 50%;
    background: var(--text-white);
  }
  .faint-horse {
    position: absolute; left: 160px; top: 140px;
    width: 134px; height: 165px;
    background: radial-gradient(ellipse 60% 55% at 60% 45%, var(--faint-tone), rgba(10,26,47,0) 100%);
  }
  .rule { position: absolute; left: 34px; height: 2px; background: var(--accent-blue); }
  .rule--top { top: 171px; width: 162px; }
  .rule--bottom { top: 266px; width: 95px; }
  .stock-claim { position: absolute; left: 34px; top: 178px; }
  .stock-claim__lead { font-size: 12px; letter-spacing: 2px; font-weight: 400; line-height: 16px; }
  .stock-claim__count {
    font-size: 34px; font-weight: 600; color: var(--accent-blue);
    line-height: 1; margin-top: 1px; letter-spacing: -0.5px;
  }
  .stock-claim__note { font-size: 10.5px; line-height: 12.5px; margin-top: 4px; }
  .company { position: absolute; left: 38px; top: 344px; }
  .company__name { font-size: 27px; font-weight: 700; line-height: 1.05; letter-spacing: 0.2px; }
  .company__tagline {
    font-size: 13.5px; font-weight: 500; color: var(--accent-blue);
    letter-spacing: 2.8px; line-height: 1.2; margin-top: 1px;
  }
  .contact {
    position: absolute; left: 38px; top: 418px;
    list-style: none; font-size: 12.5px; font-weight: 500; line-height: 20px;
  }

  /* Back */
  .distributor-label {
    position: absolute; left: 0; right: 0; top: 46px;
    text-align: center; font-size: 11.5px; font-weight: 500;
    letter-spacing: 3.6px; color: var(--accent-blue);
  }
  .partner-mark {
    position: absolute; left: 0; right: 0; top: 80px;
    display: flex; flex-direction: column; align-items: center; gap: 14px;
  }
  .partner-mark__circle {
    width: 74px; height: 74px; border-radius: 50%;
    background: var(--text-white);
  }
  .partner-mark__name {
    font-size: 32px; font-weight: 500; line-height: 1; letter-spacing: 0.5px;
  }
  .rearing-horse {
    position: absolute; left: 0; top: 262px; width: 270px; height: 252px;
    background:
      radial-gradient(ellipse 38% 30% at 62% 30%, var(--sketch-tone), rgba(10,26,47,0) 100%),
      radial-gradient(ellipse 55% 45% at 45% 62%, rgba(170, 192, 220, 0.3), rgba(10,26,47,0) 100%),
      radial-gradient(ellipse 30% 14% at 80% 65%, rgba(190, 208, 230, 0.3), rgba(10,26,47,0) 100%);
  }
</style>
</head>
<body>
<main class="sheet">
  <section class="card card--front" aria-label="Card front">
    <div class="brand-mark"><span class="brand-mark__dot"></span>harrowfields</div>
    <div class="faint-horse" role="img" aria-label="Faint line drawing of a leaping horse"></div>
    <div class="rule rule--top"></div>
    <div class="stock-claim">
      <p class="stock-claim__lead">WE HAVE OVER</p>
      <p class="stock-claim__count">15,000</p>
      <p class="stock-claim__note">items online, ship<br>Australia Wide.</p>
    </div>
    <div class="rule rule--bottom"></div>
    <div class="company">
      <h1 class="company__name">HARROWFIELD</h1>
      <p class="company__tagline">HORSE SUPPLIES</p>
    </div>
    <ul class="contact">
      <li>1300 48 62 90</li>
      <li>27 Lindqvist Rd Marrowbank Q 4587</li>
      <li>www.harrowfields.net.au</li>
    </ul>
  </section>

  <section class="card card--back" aria-label="Card back">
    <p class="distributor-label">DISTRIBUTERS OF</p>
    <div class="partner-mark">
      <span class="partner-mark__circle"></span>
      <p class="partner-mark__name">TRAILGEM</p>
    </div>
    <div class="rearing-horse" role="img" aria-label="White line drawing of a rearing horse"></div>
  </section>
</main>
</body>
</html>
```